Human Resource Consulting practice needs a business card design

We need a business card design (double sided colour) for our Human Resource (HR) consulting practice in regional New South Wales, australia. Our business name is Staff Compass. We support small and medium business across the Mid North Coast of New South Wales by providing them with outsourced HR support, services and products to help them achieve compliance with workplace legislation and across all areas of the employment lifecycle from recruitment to termination and everything in between. Our corporate colours are hot pink and black. The final design should communicate professionalism, trust, people focus.
I have attached the current (old) business card for your reference.

Target Market(s)

Business owners and high level managers

Industry/Entity Type

Business

Contact Information for Business Card

Name
Title
Phone no
Mobile no
Address
PO Box
email address
website

Colors
e34197

Requirements
Must have
• Tempate for changing business card personal details including Name, position title, mobile number, email address.
• Keep current logo and colours as per attached
• Logo must be presented in 2 colours or black only not white
Nice to have
• One side logo and graphic only other side logo and personal details
Should not have
• Should not be the same as the current version (attached) but a modern interpretation.
• Does not need a busy reverse side with our list of services as per current version. I feel this is too busy.
• No photos

```html
<!DOCTYPE html>
<html lang="en">
<head>
<meta charset="utf-8">
<title>Staff Compass – Business Card</title>
<link href="https://fonts.googleapis.com/css2?family=Exo+2:wght@400;500;600;700&display=swap" rel="stylesheet">
<style>
  :root {
    --hot-pink: #e3218f;
    --charcoal: #363636;
    --ink: #2b2b2b;
    --paper-top: #ffffff;
    --paper-bottom: #e6e6e6;
    --stage: #d3d3d3;
    --white: #ffffff;
  }
  html, body {
    margin: 0;
    padding: 0;
    width: 1200px;
    height: 869px;
    overflow: hidden;
    background: var(--stage);
    font-family: "Exo 2", sans-serif;
  }
  .canvas {
    position: relative;
    width: 1200px;
    height: 869px;
  }
  .card {
    position: absolute;
    width: 560px;
    height: 320px;
    border-radius: 3px;
    overflow: hidden;
    background: linear-gradient(160deg, var(--paper-top) 0%, var(--paper-bottom) 100%);
    box-shadow: 0 10px 26px rgba(0,0,0,0.22);
  }
  .card--front { left: 70px; top: 70px; }
  .card--back { left: 570px; top: 470px; }

  .wordmark {
    display: flex;
    align-items: center;
    gap: 10px;
    color: var(--hot-pink);
    font-weight: 700;
    white-space: nowrap;
  }
  .wordmark__dot {
    background: var(--hot-pink);
    display: block;
  }
  .card--front .wordmark {
    position: absolute;
    left: 0; right: 0; top: 0; bottom: 0;
    justify-content: center;
    font-size: 48px;
    letter-spacing: 0.5px;
  }
  .card--front .wordmark__dot { width: 12px; height: 12px; }

  .card--back .wordmark {
    position: absolute;
    left: 26px;
    top: 34px;
    font-size: 34px;
  }
  .card--back .wordmark__dot { width: 9px; height: 9px; }

  .card__bands {
    position: absolute;
    left: 0; top: 0;
    width: 560px; height: 320px;
  }
  .address {
    position: absolute;
    left: 24px;
    top: 126px;
    color: var(--white);
    font-size: 15px;
    font-weight: 500;
    letter-spacing: 0.6px;
  }
  .person {
    position: absolute;
    right: 26px;
    top: 118px;
    text-align: left;
  }
  .person__name {
    color: var(--hot-pink);
    font-size: 20px;
    font-weight: 600;
    letter-spacing: 1.2px;
    margin: 0;
  }
  .person__title {
    color: var(--ink);
    font-size: 10.5px;
    font-weight: 500;
    letter-spacing: 1px;
    margin: 2px 0 0;
  }
  .contact {
    position: absolute;
    display: flex;
    align-items: center;
    gap: 12px;
    color: var(--white);
    font-size: 14px;
    letter-spacing: 0.5px;
  }
  .contact svg { display: block; }
  .contact--web { left: 24px; top: 180px; }
  .contact--mail { left: 24px; top: 218px; }
  .contact--phone { left: 360px; top: 206px; font-size: 15px; letter-spacing: 1.6px; }
  .contact--mobile { left: 360px; top: 240px; font-size: 15px; letter-spacing: 1.6px; }
</style>
</head>
<body>
<main class="canvas">

  <section class="card card--front" aria-label="Business card front">
    <div class="wordmark"><span class="wordmark__dot"></span>Staff Compass</div>
  </section>

  <section class="card card--back" aria-label="Business card back">
    <svg class="card__bands" viewBox="0 0 560 320" aria-hidden="true">
      <polygon points="0,152 380,152 400,186 560,186 560,284 0,284" fill="var(--charcoal)"/>
      <polygon points="0,116 352,116 380,152 0,152" fill="var(--hot-pink)"/>
      <polygon points="384,152 392,152 410,180 560,180 560,186 400,186" fill="var(--hot-pink)"/>
      <rect x="0" y="284" width="560" height="36" fill="var(--hot-pink)"/>
    </svg>

    <div class="wordmark"><span class="wordmark__dot"></span>Staff Compass</div>

    <p class="address">14 Horton Street, Port Macquarie NSW</p>

    <div class="person">
      <p class="person__name">MARA ELLISON</p>
      <p class="person__title">GENERAL MANAGER</p>
    </div>

    <div class="contact contact--web">
      <svg width="24" height="24" viewBox="0 0 24 24" aria-hidden="true">
        <rect width="24" height="24" rx="3" fill="var(--white)"/>
        <circle cx="12" cy="12" r="7" fill="none" stroke="var(--charcoal)" stroke-width="1.5"/>
        <ellipse cx="12" cy="12" rx="3" ry="7" fill="none" stroke="var(--charcoal)" stroke-width="1.3"/>
        <line x1="5" y1="12" x2="19" y2="12" stroke="var(--charcoal)" stroke-width="1.3"/>
      </svg>
      <span>www.staffcompass-hr.com</span>
    </div>

    <div class="contact contact--mail">
      <svg width="24" height="24" viewBox="0 0 24 24" aria-hidden="true">
        <rect width="24" height="24" rx="3" fill="var(--white)"/>
        <rect x="5" y="7" width="14" height="10" fill="none" stroke="var(--charcoal)" stroke-width="1.5"/>
        <polyline points="5,7 12,13 19,7" fill="none" stroke="var(--charcoal)" stroke-width="1.5"/>
      </svg>
      <span>hello@staffcompass-hr.com</span>
    </div>

    <div class="contact contact--phone">
      <svg width="24" height="24" viewBox="0 0 24 24" aria-hidden="true">
        <rect width="24" height="24" rx="3" fill="var(--white)"/>
        <path d="M8 5 l3 0 l1 4 l-2 1 q1 3 4 4 l1 -2 l4 1 l0 3 q-8 1 -11 -11 z" fill="var(--charcoal)"/>
      </svg>
      <span>02 6550 4812</span>
    </div>

    <div class="contact contact--mobile">
      <svg width="24" height="24" viewBox="0 0 24 24" aria-hidden="true">
        <rect width="24" height="24" rx="3" fill="var(--white)"/>
        <rect x="8" y="4" width="8" height="16" rx="1.5" fill="var(--charcoal)"/>
        <rect x="9.5" y="6" width="5" height="10" fill="var(--white)"/>
        <circle cx="12" cy="18" r="0.9" fill="var(--white)"/>
      </svg>
      <span>02 6550 4812</span>
    </div>
  </section>

</main>
</body>
</html>
```